Business Card and Letterhead for Pimlu - modern real estate business

I need a double sided business card design for Pimlu. Please see business card brief here https://files.trelvonadocs.com/sheet/r/7QzTmWbaXLJnoPEd-kRyUgFhHsstbvCe2qfoMxDa_pz/view?mode=shared

Please feel free to design the business cards however you feel best. I am happy to give some creative freedoms and then provide feedback from there.

Please then also create a letterhead to match the business card design

Colors

Designer to choose colors to be used in the design.

Requirements
Must have
• Must be a modern, elegant business card which looks very professional

```html
<!DOCTYPE html>
<html lang="en">
<head>
<meta charset="UTF-8">
<title>Pimlu Business Card</title>
<link href="https://fonts.googleapis.com/css2?family=Michroma&family=Montserrat:wght@400;500;700&display=swap" rel="stylesheet">
<style>
  :root {
    --canvas-bg: #e6e3de;
    --card-light: #efefef;
    --card-dark: #231f20;
    --brand-red: #d71920;
    --ink: #1d1d1f;
    --faint-pink: #efc9cb;
    --white: #ffffff;
  }
  * { margin: 0; padding: 0; box-sizing: border-box; }
  html, body { width: 900px; height: 1200px; overflow: hidden; }
  body {
    background: var(--canvas-bg);
    position: relative;
    font-family: "Montserrat", Arial, sans-serif;
    color: var(--ink);
  }
  .card {
    position: absolute;
    border-radius: 18px;
    box-shadow: 0 6px 14px rgba(0,0,0,0.25);
    overflow: hidden;
  }
  .card-front {
    left: 78px; top: 137px; width: 762px; height: 433px;
    background: var(--card-light);
  }
  .card-back {
    left: 77px; top: 630px; width: 766px; height: 435px;
    background: var(--card-dark);
    display: flex; align-items: center; justify-content: center;
  }
  .portrait {
    position: absolute; left: 0; top: 0;
  }
  .agent-name {
    position: absolute; left: 40px; top: 354px; width: 320px;
    text-align: center;
    font-family: "Michroma", Arial, sans-serif;
    font-size: 27px; letter-spacing: 1px;
    color: var(--brand-red);
  }
  .vertical-wordmark {
    position: absolute; left: 426px; top: 216px;
    transform: translate(-50%, -50%) rotate(90deg);
    font-family: "Montserrat", Arial, sans-serif;
    font-weight: 500;
    font-size: 44px; letter-spacing: 2px;
    color: var(--faint-pink);
    white-space: nowrap;
  }
  .role-badge {
    position: absolute; left: 470px; top: 58px; width: 237px; height: 53px;
    background: var(--brand-red);
    color: var(--white);
    font-size: 17px; letter-spacing: 1.5px; line-height: 21px;
    padding: 6px 0 0 16px;
    text-transform: uppercase;
  }
  .role-badge strong { font-weight: 700; }
  .contact {
    position: absolute; left: 470px;
    font-size: 18px; letter-spacing: 1.6px; line-height: 25px;
    text-transform: uppercase;
  }
  .contact-direct { top: 226px; }
  .contact-web { top: 291px; font-weight: 700; }
  .contact-web span { color: var(--brand-red); }
  .contact-postal { top: 339px; }
  .back-wordmark {
    font-family: "Montserrat", Arial, sans-serif;
    font-weight: 500;
    font-size: 112px; letter-spacing: 6px;
    color: var(--brand-red);
  }
</style>
</head>
<body>
  <section class="card card-front">
    <svg class="portrait" width="400" height="360" viewBox="0 0 400 360">
      <defs>
        <linearGradient id="portrait-tone" x1="0" y1="0" x2="0" y2="1">
          <stop offset="0" stop-color="#a9b9c7"/>
          <stop offset="0.45" stop-color="#8a8f6e"/>
          <stop offset="0.75" stop-color="#3a3a3c"/>
          <stop offset="1" stop-color="#1e1e20"/>
        </linearGradient>
      </defs>
      <circle cx="199" cy="188" r="119" fill="url(#portrait-tone)" role="img" aria-label="Portrait photo of the agent outdoors"/>
      <path d="M77 144 A130 130 0 1 1 264 301" fill="none" stroke="var(--brand-red)" stroke-width="7"/>
      <path d="M264 301 A130 130 0 0 1 77 144" fill="none" stroke="var(--card-dark)" stroke-width="7"/>
    </svg>
    <p class="agent-name">JONAH MERCER</p>
    <p class="vertical-wordmark">PIMLU</p>
    <p class="role-badge">Licenced <strong>Real</strong><br><strong>Estate</strong> Agent</p>
    <p class="contact contact-direct">0412 390 518<br>jonah@pimlu.com</p>
    <p class="contact contact-web">www.<span>pimlu</span>.com</p>
    <p class="contact contact-postal">PO Box 1927<br>Darrowvale NSW 2790</p>
  </section>

  <section class="card card-back">
    <p class="back-wordmark">PIMLU</p>
  </section>
</body>
</html>
```